PowerPoint Listing Presentation for Real Estate Agency

We need a PowerPoint presentation for a new real estate brokerage team.

[[[[[[submit 1-3 sample slides for review - i will provide feedback and you can make changes if you want to - we will not be deciding on a design prior to the deadline]]]]]

******ATTN: DESIGNERS, if your skills are webdesign then just look at this like a portable website or a brochure. it should be easy enough******

NOTE: we have all the data to put into the slides. You just need to come up with the design and layout. we have a sample design that we like and have provided.

This focus will be for the home listing side of the business (a presentation for home sellers to convince them to use our services). The data and slides will present our team and the benefits, in the best light, to use our services over that of other real estate agent applying for the job. This presentation will proved facts and benefits and describe our special and unique offerings that will show a home seller why we can sell their home for more money in less time and with the least amount of hassle. The main color scheme is Dark Blue and White (we want some additional colors included - based on your creativity. otherwise the presentation will too monotone). We would like to see the use of Statistical Graphs (3-D) - data provided. We have photos of our team and a new logo (the logo could have some minor adjustment to clean it up if necessary) - also uploaded. We have about 80-90% of the information that will be put into the slides and will need to work closely to get the design and data integrated into the presentation (should be easier then it sounds). We should be able to add slides and data 'at will' over time via our master slides built into the presentation. We have a pretty good sample presentation that we like and can be used as a guideline (this is from our affiliated business network and we have full rights to all the information), it is uploaded but doesn't contain all the slide because of size limitations.

NOTE: An additional buyers presentation will be needed after we get the sellers presentation completed, which means additional work.

This should be enough to get you started and we are available if you have any questions to help you with the project. there will be around 60-70 total slides. once concept is completed it will be easy to create the slides.

Target Market(s)

home sellers. people who are moving to a new and better home or relocation for job reasons. typically more established in life

Industry/Entity Type

Real Estate

Requirements
Must have
• all the slides must be congruent. in other words, the exact same layout feel should used across the board. we are working on building our trade dress/image. Also, it must have a soft and inviting overall feel, yet show strength of ability.
Nice to have
• nice to have use of real people images when necessary. 3D graphs would be nice. clean modern look and feel, yet sophisticated and professional.
Should not have
• should not have a lot of time consuming transitions. do not include 3D stick figures or distracting moving gifs

```html
<!DOCTYPE html>
<html lang="en">
<head>
<meta charset="utf-8">
<title>Hartwell &amp; Crane – Seller Presentation Slides</title>
<link rel="stylesheet" href="https://fonts.googleapis.com/css2?family=Alike&family=Fenix&display=swap">
<style>
  :root {
    --navy: #0d2a63;
    --navy-deep: #0a2257;
    --royal: #1447b8;
    --edge-blue: #4f8fe6;
    --sky: #d7e6fb;
    --paper: #f7faff;
    --ink: #1b2436;
    --gold: #f2b705;
    --stage: #000000;
    --serif: "Alike", "Fenix", Georgia, serif;
  }
  * { box-sizing: border-box; margin: 0; padding: 0; }
  html, body { width: 1200px; height: 914px; overflow: hidden; background: var(--stage); }
  .sheet { position: relative; width: 1200px; height: 914px; }

  .slide {
    position: absolute; width: 583px; height: 437px; overflow: hidden;
    background: linear-gradient(160deg, #ffffff 0%, var(--paper) 45%, var(--sky) 100%);
    font-family: var(--serif); color: var(--ink);
  }
  .slide--title   { left: 9px;   top: 7px; }
  .slide--reasons { left: 606px; top: 7px; }
  .slide--vip     { left: 9px;   top: 465px; }
  .slide--stats   { left: 606px; top: 465px; }

  .slide__backdrop { position: absolute; inset: 0; width: 100%; height: 100%; }

  .brand-box {
    position: absolute; right: 9px; bottom: 12px; width: 194px; height: 56px;
    background: #fff; border: 2px solid var(--navy);
    display: flex; align-items: center; justify-content: center; gap: 8px;
    box-shadow: 0 0 0 2px #fff;
  }
  .brand-box__mark { width: 14px; height: 14px; background: var(--navy); }
  .brand-box__name { font-family: var(--serif); font-size: 15px; color: var(--navy); letter-spacing: 0.3px; }

  /* title slide */
  .team-photo {
    position: absolute; left: 12px; top: 55px; width: 205px; height: 382px;
    background: linear-gradient(180deg, #3a3d44 0%, #1d1f24 60%, #2a2c31 100%);
    border-radius: 60px 60px 4px 4px;
  }
  .slide__headline {
    position: absolute; left: 238px; top: 202px; font-size: 30px; font-weight: 400; color: var(--navy);
  }

  /* section headers */
  .section-head {
    position: absolute; right: 14px; display: flex; align-items: center; gap: 8px;
    font-size: 24px; color: var(--ink); font-weight: 400;
  }
  .section-head__badge {
    width: 32px; height: 32px; border-radius: 50%; background: var(--royal);
    border: 3px solid var(--navy); color: #fff; font-size: 20px;
    display: flex; align-items: center; justify-content: center;
  }
  .section-head__accent { color: var(--royal); }
  .slide--reasons .section-head { top: 12px; }
  .slide--vip .section-head, .slide--stats .section-head { top: 22px; }

  .reasons__subtitle {
    position: absolute; right: 12px; top: 55px; text-align: right;
    font-size: 13.5px; line-height: 21px; color: var(--royal);
  }

  .checklist { position: absolute; list-style: none; }
  .checklist__item { position: absolute; left: 0; padding-left: 32px; }
  .tick { position: absolute; left: 0; top: 2px; width: 22px; height: 20px; }

  .reasons .checklist__item { font-size: 14px; line-height: 21px; width: 500px; }
  .reasons { left: 34px; top: 0; }
  .reasons__label { font-weight: 700; color: var(--royal); font-size: 12.5px; }

  .benefits { left: 32px; top: 0; }
  .benefits .checklist__item { font-size: 17.5px; line-height: 30px; width: 480px; padding-left: 36px; }
  .benefits__strong { color: var(--royal); font-weight: 700; font-size: 16px; letter-spacing: 0.3px; }

  .stats { left: 30px; top: 0; }
  .stats .checklist__item { font-size: 19px; line-height: 31px; padding-left: 40px; width: 320px; }
  .stats__line { color: var(--navy-deep); }
  .stats__blue { color: var(--royal); }

  .sales-chart { position: absolute; left: 360px; top: 112px; width: 125px; height: 215px; }
</style>
</head>
<body>
<main class="sheet">

  <!-- Slide: opening -->
  <section class="slide slide--title">
    <svg class="slide__backdrop" viewBox="0 0 583 437" aria-hidden="true">
      <path d="M0 0 H190 C120 30 45 95 0 165 Z" fill="var(--edge-blue)"/>
      <path d="M0 0 H175 C110 28 40 90 0 150 Z" fill="var(--navy)"/>
      <path d="M583 118 C518 288 412 388 282 437 H583 Z" fill="var(--edge-blue)"/>
      <path d="M583 132 C522 294 420 392 302 437 H583 Z" fill="var(--navy)"/>
    </svg>
    <div class="team-photo" role="img" aria-label="Photo of the two team partners standing in dark suits"></div>
    <h1 class="slide__headline">Helping You Home</h1>
    <div class="brand-box"><span class="brand-box__mark"></span><span class="brand-box__name">HARTWELL &amp; CRANE</span></div>
  </section>

  <!-- Slide: five reasons -->
  <section class="slide slide--reasons">
    <svg class="slide__backdrop" viewBox="0 0 583 437" aria-hidden="true">
      <path d="M0 0 H160 C95 40 35 120 0 215 Z" fill="var(--edge-blue)"/>
      <path d="M0 0 H145 C85 40 28 115 0 200 Z" fill="var(--navy)"/>
      <path d="M583 128 C525 300 440 395 330 437 H583 Z" fill="var(--edge-blue)"/>
      <path d="M583 142 C530 305 448 398 350 437 H583 Z" fill="var(--navy)"/>
    </svg>
    <h2 class="section-head"><span class="section-head__badge">5</span>Biggest Reasons</h2>
    <p class="reasons__subtitle">The Hartwell &amp; Crane Team’s Success Can Be Yours<br>The 5 Biggest Reasons for The Hartwell &amp; Crane Team to Sell Your Home</p>
    <ul class="checklist reasons">
      <li class="checklist__item" style="top:124px"><svg class="tick"><use href="#tick"/></svg><span class="reasons__label">We Sell More Homes:</span> you get more experience which ensures smooth transactions and no hassles.</li>
      <li class="checklist__item" style="top:172px"><svg class="tick"><use href="#tick"/></svg><span class="reasons__label">We Sell for Top Dollar:</span> our negotiating experience and target marketing will make sure you get the most for your home.</li>
      <li class="checklist__item" style="top:224px"><svg class="tick"><use href="#tick"/></svg><span class="reasons__label">We Will Get Your Home Sold:</span> we sell the homes we list; we have an amazing success rate of 98%.</li>
      <li class="checklist__item" style="top:274px; width:440px"><svg class="tick"><use href="#tick"/></svg><span class="reasons__label">Our Track Record:</span> over 90% of our clients keep coming back to The Hartwell &amp; Crane Team for the next real estate transaction, plus you’re protected with our 5 star guarantee.</li>
      <li class="checklist__item" style="top:352px; width:345px"><svg class="tick"><use href="#tick"/></svg><span class="reasons__label">Guaranteed Sale &amp; Trade Up Program:</span> you won’t be stuck paying you mortgages or have to deal with conditional sale offers.</li>
    </ul>
    <div class="brand-box"><span class="brand-box__mark"></span><span class="brand-box__name">HARTWELL &amp; CRANE</span></div>
  </section>

  <!-- Slide: VIP benefits -->
  <section class="slide slide--vip">
    <svg class="slide__backdrop" viewBox="0 0 583 437" aria-hidden="true">
      <path d="M0 0 H205 C130 40 55 110 0 205 Z" fill="var(--edge-blue)"/>
      <path d="M0 0 H190 C120 38 48 105 0 190 Z" fill="var(--navy)"/>
      <path d="M583 120 C522 292 418 390 290 437 H583 Z" fill="var(--edge-blue)"/>
      <path d="M583 134 C528 298 428 394 310 437 H583 Z" fill="var(--navy)"/>
    </svg>
    <h2 class="section-head"><span class="section-head__badge"></span>Our VIP Seller <span class="section-head__accent">Benefits</span></h2>
    <ul class="checklist benefits">
      <li class="checklist__item" style="top:166px"><svg class="tick" style="top:5px"><use href="#tick"/></svg>Your Home Sold at a Price Acceptable to You <span class="benefits__strong">(Guaranteed in Writing)</span> or We’ll Buy it for Cash!</li>
      <li class="checklist__item" style="top:248px"><svg class="tick" style="top:5px"><use href="#tick"/></svg>Buy Any One of Our Listings and if YOU Are Not Satisfied in 24 Months <span class="benefits__strong">WE’LL BUY IT BACK!</span></li>
    </ul>
    <div class="brand-box"><span class="brand-box__mark"></span><span class="brand-box__name">HARTWELL &amp; CRANE</span></div>
  </section>

  <!-- Slide: sales figures -->
  <section class="slide slide--stats">
    <svg class="slide__backdrop" viewBox="0 0 583 437" aria-hidden="true">
      <path d="M0 0 H175 C105 40 40 120 0 215 Z" fill="var(--edge-blue)"/>
      <path d="M0 0 H160 C95 40 32 115 0 200 Z" fill="var(--navy)"/>
      <path d="M583 120 C522 292 418 390 290 437 H583 Z" fill="var(--edge-blue)"/>
      <path d="M583 134 C528 298 428 394 310 437 H583 Z" fill="var(--navy)"/>
    </svg>
    <h2 class="section-head"><span class="section-head__badge"></span>Our VIP Seller <span class="section-head__accent">Benefits</span></h2>
    <ul class="checklist stats">
      <li class="checklist__item stats__blue" style="top:146px"><svg class="tick" style="top:6px"><use href="#tick"/></svg>Number of Homes Sold 55</li>
      <li class="checklist__item stats__line" style="top:188px">Average Agent = &lt;3</li>
      <li class="checklist__item stats__line" style="top:223px"><svg class="tick" style="top:6px"><use href="#tick"/></svg>The Hartwell &amp; Crane Team<br><span class="stats__blue">SOLD 18 Times</span> More Homes<br>Then the Average Agent!</li>
    </ul>
    <svg class="sales-chart" viewBox="0 0 125 215" role="img" aria-label="3D bar: 55 homes sold in 2012">
      <polygon points="10,50 62,5 114,50 100,50 100,205 24,205 24,50" fill="var(--royal)"/>
      <polygon points="62,5 114,50 100,50 62,18" fill="#0a3a9e"/>
      <polygon points="10,50 62,5 62,18 24,50" fill="#2f66d6"/>
      <polygon points="24,50 62,50 62,205 24,205" fill="var(--navy)"/>
      <text transform="translate(52,190) rotate(-90)" fill="#fff" font-family="Alike, serif" font-size="30">55</text>
      <text transform="translate(52,150) rotate(-90)" fill="#fff" font-family="Alike, serif" font-size="14">Home sold</text>
      <text transform="translate(88,180) rotate(-90)" fill="#fff" font-family="Alike, serif" font-size="16">2012</text>
    </svg>
    <div class="brand-box"><span class="brand-box__mark"></span><span class="brand-box__name">HARTWELL &amp; CRANE</span></div>
  </section>

  <svg width="0" height="0" style="position:absolute" aria-hidden="true">
    <symbol id="tick" viewBox="0 0 22 20">
      <circle cx="10" cy="11" r="8" fill="none" stroke="var(--royal)" stroke-width="2"/>
      <path d="M5 10 L9.5 15 L19 3" fill="none" stroke="var(--navy)" stroke-width="5" stroke-linecap="round" stroke-linejoin="round"/>
      <path d="M5 10 L9.5 15 L19 3" fill="none" stroke="var(--gold)" stroke-width="2.6" stroke-linecap="round" stroke-linejoin="round"/>
    </symbol>
  </svg>
</main>
</body>
</html>
```